Veltrane Group Business Card Design

The CEO is looking for a new trendy look for his business card.
You can stay with current branding or come up with something new/creative. It can be 3D, including Medical Office buildings. You can use our logo in a variety of colors. Please include name, title, company name, company website, email address, cell number

Target Market(s)

Real Estate Development and Construction

Industry/Entity Type

Health care real estate

Contact Information for Business Card

Rohesh Kamdar, CEO M-604.781.2249 E-roheshkamdar@veltrane.com Address:4180 Lindqvist Ave, Tampa, FL 33482 www.veltrane.com

Font styles to use
Other font styles liked:
• Be creative

Requirements
Must have
• Creative, trendy look
Nice to have
• Please go to our website to get a feel- www. veltrane.com
Should not have
• small fonts

```html
<!DOCTYPE html>
<html lang="en">
<head>
<meta charset="utf-8">
<title>Veltrane Group Business Card</title>
<link rel="stylesheet" href="https://fonts.googleapis.com/css2?family=Jost:wght@300;400;600;700&display=swap">
<style>
  :root {
    --stage: #e9e6e1;
    --card-dark: #1d1c1d;
    --card-dark-glow: #3a393b;
    --silver: #d4d4d6;
    --card-light: #ffffff;
    --card-light-shade: #ececec;
    --brand-red: #a21a26;
    --brand-navy: #1f2f4d;
    --ink: #3b3b3b;
    --muted: #555555;
  }
  * { box-sizing: border-box; margin: 0; padding: 0; }
  html, body { width: 1200px; height: 900px; overflow: hidden; }
  body {
    background: var(--stage);
    font-family: "Jost", sans-serif;
    display: flex;
    flex-direction: column;
    align-items: center;
    justify-content: center;
    gap: 36px;
  }
  .card {
    width: 700px;
    height: 400px;
    border-radius: 34px;
    position: relative;
    box-shadow: 0 10px 28px rgba(0,0,0,0.18);
    overflow: hidden;
  }
  .card--front {
    background: radial-gradient(ellipse at 50% 45%, var(--card-dark-glow) 0%, var(--card-dark) 70%);
    display: flex;
    align-items: center;
    justify-content: center;
  }
  .front-wordmark {
    color: var(--silver);
    font-weight: 700;
    font-size: 76px;
    letter-spacing: -1px;
    line-height: 1;
  }
  .card--back {
    background: linear-gradient(100deg, var(--card-light) 0%, var(--card-light-shade) 55%, var(--card-light) 100%);
  }
  .back-wordmark {
    position: absolute;
    left: 52px;
    top: 54px;
    color: var(--brand-red);
    font-weight: 700;
    font-size: 58px;
    letter-spacing: -1px;
    line-height: 1;
  }
  .identity {
    position: absolute;
    right: 386px;
    bottom: 70px;
    text-align: right;
  }
  .identity__title {
    color: var(--muted);
    font-weight: 300;
    font-size: 22px;
    line-height: 1.1;
  }
  .identity__name {
    color: var(--brand-red);
    font-weight: 600;
    font-size: 24px;
    text-transform: uppercase;
    letter-spacing: 0.5px;
    white-space: nowrap;
  }
  .divider {
    position: absolute;
    left: 332px;
    bottom: 58px;
    width: 1.5px;
    height: 104px;
    background: var(--brand-navy);
  }
  .contacts {
    position: absolute;
    left: 350px;
    bottom: 58px;
    list-style: none;
    display: flex;
    flex-direction: column;
    gap: 3px;
  }
  .contacts__item {
    display: flex;
    align-items: center;
    gap: 9px;
    color: var(--ink);
    font-weight: 400;
    font-size: 17px;
    line-height: 1.4;
    white-space: nowrap;
  }
  .contacts__icon { width: 16px; height: 16px; flex: none; }
</style>
</head>
<body>
  <section class="card card--front" aria-label="Business card front">
    <p class="front-wordmark">Veltrane Group</p>
  </section>

  <section class="card card--back" aria-label="Business card back">
    <p class="back-wordmark">Veltrane Group</p>

    <div class="identity">
      <p class="identity__title">CEO</p>
      <p class="identity__name">Rohesh Kamdar</p>
    </div>

    <span class="divider"></span>

    <ul class="contacts">
      <li class="contacts__item">
        <svg class="contacts__icon" viewBox="0 0 16 16" aria-hidden="true"><rect x="4" y="1" width="8" height="14" rx="1.5" fill="none" stroke="#a21a26" stroke-width="1.6"/><rect x="7" y="12" width="2" height="1.3" fill="#a21a26"/></svg>
        604.781.2249
      </li>
      <li class="contacts__item">
        <svg class="contacts__icon" viewBox="0 0 16 16" aria-hidden="true"><rect x="1" y="3" width="14" height="10" fill="#a21a26"/><path d="M1 3 L8 9 L15 3" fill="none" stroke="#fff" stroke-width="1.3"/></svg>
        roheshkamdar@veltrane.com
      </li>
      <li class="contacts__item">
        <svg class="contacts__icon" viewBox="0 0 16 16" aria-hidden="true"><g fill="none" stroke="#a21a26" stroke-width="1.2"><circle cx="8" cy="8" r="6.5"/><ellipse cx="8" cy="8" rx="3" ry="6.5"/><path d="M1.5 8h13M2.8 4.5h10.4M2.8 11.5h10.4"/></g></svg>
        www.veltrane.com
      </li>
      <li class="contacts__item">
        <svg class="contacts__icon" viewBox="0 0 16 16" aria-hidden="true"><path d="M8 15 C4 10 3 8 3 6 a5 5 0 0 1 10 0 c0 2 -1 4 -5 9z" fill="#a21a26"/><circle cx="8" cy="6" r="1.8" fill="#fff"/></svg>
        4180 Lindqvist Ave, Tampa, FL 33482
      </li>
    </ul>
  </section>
</body>
</html>
```